CBD AgriBusiness Verdant Trophy Business Card

We are HiTec producer of medical cannabis CBD Switzerland of high quality. Our website is alpinleaf.net, we will also revisit it graphically, the winner of this contest will be the graphic designer chosen for the new design of the website. We stand out by the skill of the team, many of our engineers we win cup cannabis. I join the current map to take as an example but to revisit completely: deletion of surname and first name, modification of funds (front / back), reorganization of text info, highlighting the address of the website. three characteristics define the business card: Professional, Class, refined. The business card must be optimized for soft-touch and selective varnish printing.

Target Market(s)

Customers and Suppliers

Industry/Entity Type

Agribusiness

Contact Information for Business Card

Logo, Tél / Whatsapp, mail, url du site : alpinleaf.net

Font styles to use
Sans Serif

Requirements
Must have
• Logo of alpinleaf.net
Nice to have
• a design that stands out well on the selective varnish
Should not have
• Last name and first name

```html
<!DOCTYPE html>
<html lang="en">
<head>
<meta charset="utf-8">
<title>alpinleaf stationery</title>
<link rel="stylesheet" href="https://fonts.googleapis.com/css2?family=Open+Sans:ital,wght@0,400;0,600;0,700;1,700&display=swap">
<style>
  :root{
    --bg:#f4f4f3;
    --paper:#f0f0ee;
    --white:#ffffff;
    --green:#8cc152;
    --green-soft:#a6cf74;
    --green-deep:#3d5e1c;
    --grey:#7b7b7b;
    --ink:#333333;
    --ink-soft:#8a8a8a;
    --pattern:#e9e9e9;
  }
  *{box-sizing:border-box;margin:0;padding:0}
  html,body{width:1200px;height:800px;overflow:hidden}
  body{background:var(--bg);font-family:"Open Sans",Arial,sans-serif;color:var(--ink);position:relative}
  .piece{position:absolute;box-shadow:0 2px 6px rgba(0,0,0,.12)}
  .brand{font-family:"Open Sans",Arial,sans-serif;font-weight:700;color:var(--ink);letter-spacing:-.5px;display:flex;align-items:center;gap:.25em;line-height:1;white-space:nowrap}
  .brand .mark{display:inline-block;width:.55em;height:.55em;background:var(--green)}
  .contact-list{list-style:none;display:flex;flex-direction:column}
  .contact-list li{display:flex;align-items:center;color:var(--ink);white-space:nowrap}
  .contact-list .dot{border-radius:50%;background:var(--green);flex:none}

  /* letterhead */
  .letterhead{left:310px;top:76px;width:331px;height:471px;background:var(--paper)}
  .letterhead .brand{position:absolute;left:22px;top:27px;font-size:24px}
  .letterhead .divider{position:absolute;left:180px;top:15px;width:2px;height:43px;background:var(--green)}
  .letterhead .contact-list{position:absolute;left:234px;top:18px;gap:5px;font-size:4.5px}
  .letterhead .contact-list .dot{width:8px;height:8px;margin-right:6px}
  .letter{position:absolute;left:22px;top:134px;width:292px}
  .letter .greeting{font-size:7.5px;margin-bottom:16px}
  .letter p{font-size:5.6px;line-height:1.6;color:var(--ink-soft);margin-bottom:8px}
  .letter .regards{font-size:7px;margin-top:14px}
  .letter .name{font-size:7px;margin-top:8px}
  .letter .role{font-size:5px;color:var(--ink-soft)}
  .signature{margin-top:8px;width:62px;height:10px;background:linear-gradient(90deg,#cfcfcf,#e6e6e6)}

  /* folder */
  .folder{left:662px;top:49px;width:367px;height:499px;background:var(--grey)}
  .folder .flap{position:absolute;right:0;top:0;width:50px;height:100%;border-left:2px solid #8c8c8c;background:#808080}
  .folder .brand{position:absolute;left:76px;top:418px;font-size:44px;color:#555}

  /* cards */
  .card{width:147px;height:84px;background:var(--white);overflow:hidden}
  .card svg{position:absolute;inset:0}
  .card-front{left:147px;top:567px}
  .card-front .brand{position:absolute;left:32px;top:32px;font-size:18px}
  .card-front .url{position:absolute;left:62px;top:69px;font-size:4px;font-weight:600}
  .card-back{left:148px;top:665px}
  .card-back .brand{position:absolute;left:8px;top:13px;font-size:10px}
  .card-back .site{position:absolute;left:80px;top:14px;font-size:6px;font-weight:700;color:var(--green-deep);letter-spacing:-.2px}
  .card-back .contact-list{position:absolute;left:8px;top:40px;gap:6px;font-size:4px}
  .card-back .contact-list .dot{width:7px;height:7px;margin-right:6px}

  /* compliments slip */
  .slip{left:310px;top:573px;width:349px;height:175px;background:var(--paper)}
  .slip .title{position:absolute;right:25px;top:19px;font-size:10px;font-weight:700;font-style:italic;color:var(--green)}
  .slip .brand{position:absolute;left:16px;top:141px;font-size:18px}
  .slip .divider{position:absolute;left:131px;top:137px;width:1px;height:22px;background:var(--green)}
  .slip .divider.second{left:226px}
  .slip .contact-list{position:absolute;left:141px;top:137px;gap:3px;font-size:3px}
  .slip .contact-list .dot{width:5px;height:5px;margin-right:5px}
  .slip .address{position:absolute;left:249px;top:144px;font-size:6.5px}

  /* envelope */
  .envelope{left:674px;top:570px;width:351px;height:175px;background:var(--grey)}
  .envelope .flap{position:absolute;left:2px;top:0;right:0;height:49px;background:#7d7d7d;border-radius:0 0 10px 10px;box-shadow:0 1px 2px rgba(0,0,0,.25)}
  .envelope .brand{position:absolute;left:74px;top:88px;font-size:38px;color:#555}
</style>
</head>
<body>

<section class="piece letterhead">
  <div class="brand"><span class="mark"></span>alpinleaf</div>
  <span class="divider"></span>
  <ul class="contact-list">
    <li><span class="dot"></span>office@alpinleaf.net</li>
    <li><span class="dot"></span>Tel. +41 79 000 12 34</li>
    <li><span class="dot"></span>www.alpinleaf.net</li>
  </ul>
  <div class="letter">
    <div class="greeting">Dear sir/Madam,</div>
    <p>Lorem ipsum dolor sit amet, an vel recteque dissentiet, detracto albucius platonem ex vel, eros repudiandae cu. Atqui aliquando nec an, unum graece adolescens vel ad. Id odio scae has, iudico euismod atomorum ius ea, cum ea honestatis quaerendum theophrastus. Mea honestatis quaerendum theophrastus. Mea</p>
    <p>Lorem ipsum dolor sit amet, an vel recteque dissentiet, detracto albucius platonem ex vel, eros repudiandae cu. Atqui aliquando nec an, unum graece adolescens vel ad. Id odio scae has, iudico euismod atomorum ius ea, cum ea honestatis quaerendum theophrastus. Mea doming repudiandae ex, cu cum civibus assentior posidonium. Quo etiam pertinax ex, te eros repudiandae cu. Atqui aliquando nec an, unum graece adolescens vel ad. Id odio scae honestatis quaerendum theophrastus. Mea</p>
    <p>Lorem ipsum dolor sit amet, an vel recteque dissentiet, detracto albucius platonem ex vel, eros repudiandae cu. Atqui aliquando nec an, unum graece adolescens vel ad. Id odio scae has, iudico euismod atomorum ius ea, cum ea honestatis quaerendum theophrastus. Mea honestatis quaerendum theophrastus. Mea</p>
    <p>eros repudiandae cu. Atqui aliquando nec an, unum graece adolescens vel ad. Id odio scae honestatis quaerendum theophrastus. Mea posidonium. Quo etiam pertinax ex, te etiam pertinax ex, te</p>
    <div class="regards">Kind Regards</div>
    <div class="name">Martin Keller</div>
    <div class="role">CEO / Founder</div>
    <div class="signature" role="img" aria-label="Handwritten signature"></div>
  </div>
</section>

<section class="piece folder">
  <div class="flap"></div>
  <div class="brand"><span class="mark"></span>alpinleaf</div>
</section>

<section class="piece card card-front">
  <svg width="147" height="84" viewBox="0 0 147 84">
    <rect width="147" height="84" fill="var(--green-soft)"/>
    <path d="M42 0 H147 V84 H38 C14 70 10 18 42 0 Z" fill="var(--white)"/>
    <path d="M88 0 H147 V84 H104 C120 60 118 24 88 0 Z" fill="var(--pattern)" role="img" aria-label="Fine geometric line network pattern"/>
  </svg>
  <div class="brand"><span class="mark"></span>alpinleaf</div>
  <div class="url">www.alpinleaf.net</div>
</section>

<section class="piece card card-back">
  <svg width="147" height="84" viewBox="0 0 147 84">
    <rect width="147" height="84" fill="var(--white)"/>
    <path d="M78 0 H147 V84 H112 C92 60 86 30 78 0 Z" fill="var(--green-soft)" role="img" aria-label="Green band with geometric line network pattern"/>
  </svg>
  <div class="brand"><span class="mark"></span>alpinleaf</div>
  <div class="site">ALPINLEAF.NET</div>
  <ul class="contact-list">
    <li><span class="dot"></span>office@alpinleaf.net</li>
    <li><span class="dot"></span>Tel. +41 79 000 12 34</li>
    <li><span class="dot"></span>www.alpinleaf.net</li>
  </ul>
</section>

<section class="piece slip">
  <div class="title">With Compliments ...</div>
  <div class="brand"><span class="mark"></span>alpinleaf</div>
  <span class="divider"></span>
  <ul class="contact-list">
    <li><span class="dot"></span>office@alpinleaf.net</li>
    <li><span class="dot"></span>Tel. +41 79 000 12 34</li>
    <li><span class="dot"></span>www.alpinleaf.net</li>
  </ul>
  <span class="divider second"></span>
  <div class="address">Address</div>
</section>

<section class="piece envelope">
  <div class="flap"></div>
  <div class="brand"><span class="mark"></span>alpinleaf</div>
</section>

</body>
</html>
```